Real estate business card

I need a business card for my real estate company. I help clients buy and sell properties. I would like to keep the design very simple and professional. I would like the design to convey professionalism, safety and trust. I prefer no graphics but a simple logo design would be nice if that is part of what you do.
Updates

Please keep the designs simple. No high-rise buildings please. 

Project Deadline Extended
Reason: My design has not been finalized.

Target Market(s)

Age group 30-60 mostly affluent

Industry/Entity Type

Real Estate

Contact Information for Business Card

Velmont Realtors
Gregory Velmont, Broker
4815 Brindle Ave. #263, La Crescenta, CA 91206

Requirements
Nice to have
• Logo can be combination of my initials GV or just Z or a simple geometric shape? Please see "Desig Ideas" attachment. No pics of houses or shaking hands, dollar bills, $, %, etc...
Please use fonts similar to Helvetica for a clean, modern look (think Northern European design, simple, clean yet bold)

Also use font colors such as blue, grey in different shades. Use pastel colors if better.

```html
<!DOCTYPE html>
<html lang="en">
<head>
<meta charset="utf-8">
<title>Velmont Realtors – Business Card</title>
<link href="https://fonts.googleapis.com/css2?family=Exo+2:wght@400;500&family=Cinzel:wght@500&display=swap" rel="stylesheet">
<style>
  :root{
    --backdrop:#9a9a9a;
    --card-light:#ffffff;
    --card-shade:#e4e5e7;
    --ink:#2b2b2b;
    --ink-soft:#555;
    --rule-blue:#3f7fd0;
    --rule-cyan:#5fc6e6;
    --pill-dark:#333333;
    --accent-blue:#3d7fd6;
    --accent-cyan:#6fd0ea;
  }
  *{box-sizing:border-box;margin:0;padding:0}
  html,body{width:1200px;height:894px;overflow:hidden}
  body{background:var(--backdrop);position:relative;font-family:"Exo 2",sans-serif;color:var(--ink)}
  .card{
    position:absolute;top:292px;width:540px;height:309px;overflow:hidden;
    background:linear-gradient(160deg,var(--card-light) 35%,var(--card-shade) 100%);
    box-shadow:0 6px 18px rgba(0,0,0,.25);
  }
  .card--contact{left:40px}
  .card--brand{left:620px}

  /* contact side */
  .holder{position:absolute;left:40px;top:30px}
  .holder__name{font-size:25px;font-weight:500;letter-spacing:.5px;line-height:1}
  .holder__role{font-size:9.5px;letter-spacing:1px;color:var(--ink-soft);margin-top:4px}
  .rule{position:absolute;height:2px;background:linear-gradient(90deg,var(--rule-blue),var(--rule-cyan) 60%,var(--rule-blue))}
  .rule--title{left:40px;top:80px;width:155px;height:1.5px}
  .contact-list{position:absolute;left:40px;top:96px;font-size:14px;line-height:21px;display:grid;grid-template-columns:68px auto;column-gap:6px}
  .contact-list dt{color:var(--ink)}
  .contact-list dd{color:var(--ink)}
  .rule--mid{left:40px;top:186px;width:290px}
  .address{position:absolute;left:40px;top:196px;display:flex;align-items:center;gap:8px;font-size:13px}
  .address svg{width:12px;height:16px;flex:none}
  .rule--low1{left:40px;top:240px;width:460px}
  .rule--low2{left:40px;top:268px;width:500px}
  .accent-pill{
    position:absolute;right:-40px;top:120px;width:175px;height:70px;border-radius:35px;
    background:radial-gradient(circle at 40% 45%,var(--accent-cyan),var(--accent-blue) 80%);
  }

  /* brand side */
  .mark-area{
    position:absolute;left:30px;top:0;width:210px;height:180px;border-radius:0 0 50% 50%;
    background:radial-gradient(ellipse at 50% 40%,rgba(111,208,234,.55),rgba(61,127,214,.35) 55%,rgba(228,229,231,0) 80%);
  }
  .brand-pill{
    position:absolute;right:0;top:205px;height:52px;width:290px;
    background:var(--pill-dark);border-radius:26px 0 0 26px;
    display:flex;align-items:center;justify-content:center;
  }
  .brand-pill__name{font-family:"Cinzel",serif;font-weight:500;font-size:22px;color:#fff;letter-spacing:1px}
</style>
</head>
<body>
  <section class="card card--contact" aria-label="Contact side">
    <div class="holder">
      <p class="holder__name">Gregory Velmont</p>
      <p class="holder__role">GENERAL MANAGER</p>
    </div>
    <div class="rule rule--title"></div>
    <dl class="contact-list">
      <dt>Phone:</dt><dd>555 204 8816</dd>
      <dt>Fax:</dt><dd>555 204 8817</dd>
      <dt>Email:</dt><dd>gregory@velmontrealtors.com</dd>
      <dt>website:</dt><dd>www.velmontrealtors.com</dd>
    </dl>
    <div class="rule rule--mid"></div>
    <p class="address">
      <svg viewBox="0 0 12 16" aria-hidden="true"><path d="M6 0a6 6 0 0 0-6 6c0 4.5 6 10 6 10s6-5.5 6-10a6 6 0 0 0-6-6zm0 8.5A2.5 2.5 0 1 1 6 3.5a2.5 2.5 0 0 1 0 5z" fill="#2b2b2b"/></svg>
      4815 Brindle Ave. #263, La Crescenta, CA 91206
    </p>
    <div class="rule rule--low1"></div>
    <div class="rule rule--low2"></div>
    <div class="accent-pill"></div>
  </section>

  <section class="card card--brand" aria-label="Brand side">
    <div class="mark-area" role="img" aria-label="Decorative blue symbol area"></div>
    <div class="brand-pill"><span class="brand-pill__name">Velmont Realtors</span></div>
  </section>
</body>
</html>
```